Auntie Verdict Billboard

I need a billboard designed for a Personal Injury Law firm. I need to simple not busy. I am attaching the following as suggestions to use. Need good colors that show up from Road Simple that can leave people associating injury lawyer with Auntie Verdict. Big picture of Dottie. Need Auntieverdict.com and 555-417-9038 to be big. possiblly let the emojis do the talking for personal injury and money settlement. Colors for logo should be similar to website auntieverdict.com
Updates

Billboard size. 10.5ft. X 36ft.

Target Market(s)

Car Accident Victims

Font styles to use
Sans Serif

Requirements
Must have
• Picture of Dottie. auntieverdict.com. 555-417-9038. message needs to be clear that she is a personal injury attorney. Clear simple message. Colors bold and visable to highway drivers
Should not have
• Busy ad.

```html
<!DOCTYPE html>
<html lang="en">
<head>
<meta charset="utf-8">
<title>Auntie Verdict Billboard</title>
<link rel="stylesheet" href="https://fonts.googleapis.com/css2?family=Lato:wght@400;700&family=Open+Sans:wght@700;800&display=swap">
<style>
  :root {
    --backdrop: #777777;
    --board: #ffffff;
    --panel-grey: #f1f1f1;
    --navy: #0a4a8c;
    --red: #b81f25;
    --ink: #1c1c1c;
    --white: #ffffff;
  }
  * { margin: 0; padding: 0; box-sizing: border-box; }
  html, body { width: 1200px; height: 792px; overflow: hidden; }
  body { background: radial-gradient(circle at 50% 45%, #8a8a8a, var(--backdrop) 70%, #5f5f5f); }
  .stage { position: relative; width: 1500px; height: 990px; transform: scale(0.8); transform-origin: 0 0; }

  .billboard { position: absolute; left: 71px; width: 1359px; height: 397px; background: var(--board); overflow: hidden; }
  .billboard--classic { top: 65px; }
  .billboard--angled { top: 511px; }

  .billboard__shapes { position: absolute; inset: 0; }

  .portrait {
    position: absolute; bottom: 0;
    background: linear-gradient(180deg, #1a1a1f 0%, #2a2530 35%, #c99a86 38%, #1b1b22 55%, #111318 100%);
    border-radius: 140px 140px 0 0;
  }
  .billboard--classic .portrait { left: 66px; top: 10px; width: 321px; }
  .billboard--angled .portrait { left: 46px; top: 10px; width: 320px; }

  .firm { position: absolute; white-space: nowrap; }
  .billboard--classic .firm { left: 436px; top: 78px; }
  .billboard--angled .firm { left: 459px; top: 104px; }

  .firm-name {
    display: flex; align-items: baseline; gap: 10px;
    font-family: "Lato", sans-serif; font-weight: 700; font-size: 34px;
    letter-spacing: 2px; color: var(--ink); line-height: 1;
  }
  .firm-name__mark { width: 20px; height: 20px; background: var(--red); align-self: center; }
  .firm-name__suffix { font-size: 12px; letter-spacing: 1px; }

  .firm-tagline {
    margin: 8px 0 0 120px;
    font-family: "Lato", sans-serif; font-weight: 700; font-size: 16px;
    letter-spacing: 7px; color: var(--red); line-height: 1;
  }

  .art { position: absolute; }
  .art--injured { border-radius: 50%; background: radial-gradient(circle at 45% 40%, #ffd94a, #f0a21a 70%, #d98a10); }
  .art--settlement { border-radius: 10px; background: linear-gradient(160deg, #6b3d22 0%, #4a2815 55%, #8fae7c 75%, #3c2010 100%); }
  .billboard--classic .art--injured { left: 904px; top: 30px; width: 160px; height: 137px; }
  .billboard--classic .art--settlement { left: 1114px; top: 25px; width: 155px; height: 150px; }
  .billboard--angled .art--injured { left: 959px; top: 29px; width: 150px; height: 126px; }
  .billboard--angled .art--settlement { left: 1169px; top: 26px; width: 126px; height: 126px; }

  .headline {
    position: absolute; font-family: "Open Sans", sans-serif; font-weight: 800;
    color: var(--navy); white-space: nowrap; line-height: 1;
  }
  .billboard--classic .headline { left: 426px; top: 178px; font-size: 104px; letter-spacing: -1px; }
  .billboard--angled .headline { left: 417px; top: 165px; font-size: 106px; letter-spacing: -1px; }

  .contact-band { position: absolute; display: flex; align-items: center; color: var(--white); }
  .billboard--classic .contact-band { left: 384px; top: 296px; right: 0; height: 101px; background: var(--red); padding-left: 45px; }
  .billboard--angled .contact-band { left: 418px; top: 277px; width: 940px; height: 120px; }

  .phone { font-family: "Open Sans", sans-serif; font-weight: 800; white-space: nowrap; line-height: 1; }
  .billboard--classic .phone { font-size: 76px; letter-spacing: -1px; }
  .billboard--angled .phone { font-size: 88px; letter-spacing: -1px; }

  .divider { width: 2px; height: 56px; background: rgba(255,255,255,0.8); margin: 0 28px 0 30px; }
  .website { font-family: "Lato", sans-serif; font-weight: 400; font-size: 16px; letter-spacing: 3px; text-transform: uppercase; white-space: nowrap; }
  .website strong { font-weight: 700; }
</style>
</head>
<body>
<main class="stage">

  <section class="billboard billboard--classic" aria-label="Billboard, classic layout">
    <div class="portrait" role="img" aria-label="Portrait photo of attorney Dottie in a dark blazer"></div>
    <div class="firm">
      <div class="firm-name"><span class="firm-name__mark"></span>HARLOW LAW FIRM <span class="firm-name__suffix">PLLC</span></div>
      <div class="firm-tagline">AUNTIE VERDICT</div>
    </div>
    <div class="art art--injured" role="img" aria-label="Bandaged injured emoji"></div>
    <div class="art art--settlement" role="img" aria-label="Gavel resting on a stack of cash"></div>
    <h1 class="headline">AUNTIE VERDICT</h1>
    <div class="contact-band">
      <span class="phone">555-417-9038</span>
      <span class="divider"></span>
      <span class="website">www.<strong>auntieverdict</strong>.com</span>
    </div>
  </section>

  <section class="billboard billboard--angled" aria-label="Billboard, angled layout">
    <svg class="billboard__shapes" width="1359" height="397" viewBox="0 0 1359 397" aria-hidden="true">
      <polygon points="0,0 387,0 270,397 0,397" fill="var(--panel-grey)"/>
      <polygon points="387,0 441,0 324,397 270,397" fill="var(--red)"/>
      <polygon points="441,0 459,0 342,397 324,397" fill="var(--navy)"/>
      <polygon points="355,277 1339,277 1289,397 320,397" fill="var(--red)"/>
      <polygon points="1359,237 1359,397 1289,397" fill="var(--navy)"/>
    </svg>
    <div class="portrait" role="img" aria-label="Portrait photo of attorney Dottie in a dark blazer"></div>
    <div class="firm">
      <div class="firm-name"><span class="firm-name__mark"></span>HARLOW LAW FIRM <span class="firm-name__suffix">PLLC</span></div>
    </div>
    <div class="art art--injured" role="img" aria-label="Bandaged injured emoji"></div>
    <div class="art art--settlement" role="img" aria-label="Gavel resting on a stack of cash"></div>
    <h2 class="headline">AUNTIE VERDICT</h2>
    <div class="contact-band">
      <span class="phone">CALL: 555-417-9038</span>
    </div>
  </section>

</main>
</body>
</html>
```